military training website velmotrail.com

I have a website that someone designed I am not happy with. It looks like the designer did not have the artistic ability to make a quality product. the power points are ideas that I had for the website. the business proposal was designed by someone else, and I like the style and font used, the website should reflect this document. The main part of the website should be informational with few pictures, maybe some background images behind or off to the side of the text. I would like to include a generic map with four locations marked, which, when you hover the cursor over them, show a picture of the actual location with an artistic effect or blurred so it doesn't look like a plivora atlas snip, and a picture that resembles what services are offered there, along with the text description, pictures can be found in the documents I attached, also can be stock images. this is outlined in the power points roughly.
Want to have the side menu of the major topics, or at the top, and scroll down a single page to find all of the information we have to offer

Target Market(s)

Special operations military

Industry/Entity Type

military

Coding

Coded - Design and coding required

Number of Pages Required

1 page

Other font styles liked:
• Agency FB

Colors
0054AA
0677BA
7BADD7
CADEEF
E8F1F8
00AB8E
00BBA5
67D7C9
C6EFE9
E9F9F6

Requirements
Must have
• interactive "map"
Nice to have
• professional design features to make it look like a professional website, not a beginner designer

```html
<!DOCTYPE html>
<html lang="en">
<head>
<meta charset="utf-8">
<title>Velmo Trail — Special Operations Training</title>
<link rel="stylesheet" href="https://fonts.googleapis.com/css2?family=IBM+Plex+Sans:wght@600;700&family=Roboto:wght@400;500;700&display=swap">
<style>
:root{
  --navy:#0f1d3b;
  --navy-deep:#0b1630;
  --blue:#4a7aab;
  --blue-light:#7badd7;
  --text:#555b66;
  --text-dark:#2f3440;
  --white:#ffffff;
  --field-border:#e3e6ea;
}
*{box-sizing:border-box;margin:0;padding:0}
html,body{width:1200px;height:4181px;overflow:hidden}
body{position:relative;background:var(--white);font-family:"Roboto",sans-serif;color:var(--text)}
.abs{position:absolute}

/* top bar */
.topbar{left:0;top:0;width:1200px;height:36px;background:var(--navy);color:var(--white);font-size:12px}
.social{left:143px;top:12px;display:flex;gap:12px}
.social span{width:11px;height:11px;border-radius:50%;background:var(--white);display:block}
.phone{left:313px;top:11px;display:flex;align-items:center;gap:8px}
.address{right:145px;top:11px;display:flex;align-items:center;gap:8px}

/* nav */
.nav{left:0;top:36px;width:1200px;height:54px;background:var(--white);box-shadow:0 1px 3px rgba(0,0,0,.08);z-index:2}
.nav a{position:absolute;top:22px;font-size:13.5px;font-weight:500;color:var(--navy);text-decoration:none;letter-spacing:.2px}
.brand{left:522px;top:0;width:156px;height:152px;border-radius:50%;background:var(--white);z-index:3;display:flex;align-items:center;justify-content:center;box-shadow:0 2px 6px rgba(0,0,0,.15)}
.brand-inner{width:128px;height:128px;border-radius:50%;background:var(--navy);display:flex;align-items:center;justify-content:center;color:var(--white);font-family:"IBM Plex Sans",sans-serif;font-weight:700;font-size:19px;text-align:center;line-height:1.1}

/* hero */
.hero{left:0;top:90px;width:1200px;height:600px;background:linear-gradient(180deg,#6f6a5f 0%,#8a7a5c 35%,#5b4a34 62%,#3d3426 100%)}
.hero-title{right:145px;top:222px;font-family:"IBM Plex Sans",sans-serif;font-weight:700;font-size:56px;letter-spacing:1px;color:var(--white)}
.hero-title .dark{color:var(--navy)}
.hero-text{right:145px;top:302px;width:540px;text-align:right;color:var(--white);font-size:16px;line-height:25px;font-weight:500}
.hero-curve{left:0;top:480px}

/* sections */
.heading{left:0;width:1200px;text-align:center;font-family:"IBM Plex Sans",sans-serif;font-weight:700;font-size:36px;color:var(--navy-deep);letter-spacing:.5px}
.heading .accent{color:var(--blue)}
.rule{left:532px;width:136px;height:4px;background:var(--navy)}
.rule.blue{background:var(--blue);left:568px;width:64px}
.para{left:146px;width:910px;text-align:center;font-size:15px;line-height:25.5px;color:var(--text-dark)}
.para.light{color:var(--text)}

.features{left:146px;top:1032px;width:470px;list-style:none;font-size:13.5px;line-height:25.5px;color:var(--text)}
.features li{position:relative;padding-left:25px;margin-bottom:11px}
.features li::before{content:"";position:absolute;left:0;top:7px;width:12px;height:12px;border-radius:50%;background:var(--navy)}
.features li::after{content:"";position:absolute;left:3px;top:10px;width:4px;height:4px;border-top:2px solid #fff;border-right:2px solid #fff;transform:rotate(45deg)}
.feature-photo{left:600px;top:1000px;width:600px;height:812px;background:radial-gradient(ellipse at 62% 50%,#b89a6c 0%,#c9b08a 40%,rgba(230,218,198,.6) 70%,rgba(255,255,255,0) 88%)}

.map-band{left:0;top:1881px;width:1200px;height:365px;background:var(--navy)}
.map-title{color:var(--white)}
.map-frame{left:192px;top:2025px;width:816px;height:400px;background:radial-gradient(ellipse at 55% 45%,#c9ae82 0%,#a68b62 55%,#7d6646 100%);box-shadow:0 22px 30px -10px rgba(0,0,0,.35);border:2px solid #e7dcc6}
.pin{position:absolute}

/* form */
.field{height:47px;border:1px solid var(--field-border);background:var(--white);box-shadow:0 1px 3px rgba(0,0,0,.04);font-size:12.5px;color:#8a8f98;padding:15px 18px;display:flex;align-items:flex-start;gap:7px}
.field svg{flex:none;margin-top:1px}
.button{left:502px;top:3168px;width:196px;height:46px;border-radius:23px;background:var(--blue);color:var(--white);font-weight:700;font-size:14.5px;display:flex;align-items:center;justify-content:center;gap:8px;letter-spacing:.3px}

/* gallery */
.tile{box-shadow:0 3px 8px rgba(0,0,0,.12)}
.dots{left:574px;top:4031px;display:flex;gap:8px}
.dots span{width:11px;height:11px;border-radius:50%;background:#dfe2e6}
.dots span.on{background:var(--navy)}

.footer{left:0;top:4118px;width:1200px;height:63px;background:var(--navy);color:var(--white);font-size:14px}
.footer .copy{left:0;width:1200px;top:22px;text-align:center}
.footer .code{right:24px;top:28px;font-size:11px}
</style>
</head>
<body>

<header>
  <div class="abs topbar">
    <div class="abs social" aria-label="Social links"><span></span><span></span><span></span><span></span></div>
    <div class="abs phone">
      <svg width="11" height="11" viewBox="0 0 24 24"><path fill="#7badd7" d="M6.6 10.8a15.1 15.1 0 0 0 6.6 6.6l2.2-2.2a1 1 0 0 1 1-.25 11.4 11.4 0 0 0 3.6.57 1 1 0 0 1 1 1V20a1 1 0 0 1-1 1A17 17 0 0 1 3 4a1 1 0 0 1 1-1h3.5a1 1 0 0 1 1 1c0 1.25.2 2.45.57 3.57a1 1 0 0 1-.25 1z"/></svg>
      +1-888-888-8888
    </div>
    <div class="abs address">
      <svg width="9" height="12" viewBox="0 0 12 16"><path fill="#7badd7" d="M6 0a6 6 0 0 0-6 6c0 4.5 6 10 6 10s6-5.5 6-10a6 6 0 0 0-6-6zm0 8.2A2.2 2.2 0 1 1 6 3.8a2.2 2.2 0 0 1 0 4.4z"/></svg>
      11201 Lorem ipsum dolor sit amet, consectetur
    </div>
  </div>
  <nav class="abs nav">
    <a style="left:143px">MISSION</a>
    <a style="left:252px">WHAT WE PROVIDE</a>
    <a style="left:430px">MAP</a>
    <a style="left:718px">QUALIFICATIONS</a>
    <a style="left:880px">CONTACT</a>
    <a style="left:995px">GALLERY</a>
  </nav>
  <div class="abs brand"><div class="brand-inner">VELMO<br>TRAIL</div></div>
</header>

<section>
  <div class="abs hero" role="img" aria-label="Photo of two soldiers on an airfield at dusk directing an aircraft"></div>
  <h1 class="abs hero-title"><span class="dark">MASTER</span> THE MISSION</h1>
  <p class="abs hero-text">Pioneering realistic training within a strategic theater across the full spectrum of SOF capabilities, liberating warriors from the shackles of logistical burdens and unleashing their full potential to vanquish adversaries.</p>
  <svg class="abs hero-curve" width="1200" height="220" viewBox="0 0 1200 220">
    <path d="M0 60 C250 170 500 210 720 190 C950 170 1100 110 1200 40 L1200 220 L0 220 Z" fill="#ffffff"/>
    <path d="M0 60 C150 130 280 165 360 180 C250 175 120 140 0 90 Z" fill="#4a7aab"/>
    <path d="M300 175 C500 215 760 215 1000 150 C860 200 560 225 300 175 Z" fill="#4a7aab"/>
    <path d="M280 170 C520 205 820 195 1200 40 L1200 60 C880 200 560 210 280 170 Z" fill="#0f1d3b"/>
  </svg>
</section>

<section>
  <h2 class="abs heading" style="top:780px">WHAT WE <span class="accent">PROVIDE</span></h2>
  <div class="abs rule" style="top:832px"></div>
  <p class="abs para" style="top:864px">At Velmo Trail, we draw upon years of invaluable experience gained from training at SOF facilities worldwide. Our journey has culminated in the creation of an all-encompassing training site tailored to meet the exacting needs of SOF operators. We provide a comprehensive range of training modalities meticulously crafted to enhance SOF tactics. Anchored by an unwavering commitment to realism and operational effectiveness, we ensure that your warriors are fully prepared to conquer the most demanding challenges they may face.</p>
  <div class="abs feature-photo" role="img" aria-label="Photo of two special operations soldiers in camouflage moving across desert terrain"></div>
  <ul class="abs features">
    <li>Precision Marksmanship: Utilizing Tier 1 level instructors alongside seasoned local tactical shooting experts, our comprehensive programs incorporate practice with both steel and paper targets, conducted across multiple shooting locations for varied training environments.</li>
    <li>Immersive Scenarios: We have transformed a former Soviet military stronghold into a dynamic training environment, meticulously furnished with explosives, pyrotechnics, and a live Opposition Force for verisimilar assault scenarios. Underground lays an intricate tunnel system ideal for confined-space rescue and medical training.</li>
    <li>Airfield Dominance: With a sprawling 7000ft runway available, we provide an expansive canvas for a myriad of airfield operations, including seizures, static line operations, military free fall, and helicopter insertion and extraction techniques.</li>
    <li>JTAC Support: Our team comprises skilled JTACs ready to replicate aircraft in Close Air Support simulations, guaranteeing operators engage in authentic training for air-to-ground coordination, sharpening the skills needed to execute precision strikes with unmatched effectiveness.</li>
    <li>Tactical Vehicles: Our designated area enables rigorous vehicular-based training, empowering operators to navigate terrain with confidence and precision.</li>
    <li>Comfortable Lodging and Facilities: We offer on-site accommodation and mission planning rooms, complete with meticulously prepared meals, as well as sauna and other recreational and fitness amenities. Additionally, transportation services can be readily arranged, ensuring operators are well-rested and fully prepared to engage in rigorous training exercises.</li>
    <li>Cultural Immersion: Consider enriching your experience in this captivating region. Allow us to organize a cultural day, including a traditional Estonian sauna and grill experience, a guided tour of historical sites in Tallinn, and an evening filled with vibrant urban nightlife.</li>
  </ul>
</section>

<section>
  <div class="abs map-band"></div>
  <h2 class="abs heading map-title" style="top:1935px">MAP</h2>
  <div class="abs rule blue" style="top:1985px"></div>
  <div class="abs map-frame" role="img" aria-label="Illustrated map of the training compound with airfield, buildings and ranges">
    <svg class="pin" style="left:302px;top:95px" width="34" height="44" viewBox="0 0 34 44"><path d="M17 1C8 1 1 8 1 17c0 11 16 26 16 26s16-15 16-26C33 8 26 1 17 1z" fill="#fff"/><circle cx="17" cy="17" r="8" fill="#0f1d3b"/></svg>
    <svg class="pin" style="left:506px;top:32px" width="34" height="44" viewBox="0 0 34 44"><path d="M17 1C8 1 1 8 1 17c0 11 16 26 16 26s16-15 16-26C33 8 26 1 17 1z" fill="#fff"/><circle cx="17" cy="17" r="8" fill="#0f1d3b"/></svg>
    <svg class="pin" style="left:576px;top:183px" width="34" height="44" viewBox="0 0 34 44"><path d="M17 1C8 1 1 8 1 17c0 11 16 26 16 26s16-15 16-26C33 8 26 1 17 1z" fill="#fff"/><circle cx="17" cy="17" r="8" fill="#0f1d3b"/></svg>
    <svg class="pin" style="left:254px;top:224px" width="34" height="44" viewBox="0 0 34 44"><path d="M17 1C8 1 1 8 1 17c0 11 16 26 16 26s16-15 16-26C33 8 26 1 17 1z" fill="#fff"/><circle cx="17" cy="17" r="8" fill="#0f1d3b"/></svg>
  </div>
  <p class="abs para light" style="top:2472px;font-size:13.5px">At Velmo Trail OÜ, our paramount mission is to extend our hospitality to your esteemed team, immersing you in dynamic and authentic training scenarios that cover every aspect of your SOF prowess. We take charge of the logistical challenges, allowing your team to fully concentrate on mastering the mission in Eastern Europe. Our steadfast dedication ensures that every SOF warrior attains the pinnacle of performance and resolute readiness, empowering you to excel in your noble mission: the relentless pursuit of absolute victory with decisive force!</p>
</section>

<section>
  <h2 class="abs heading" style="top:2650px">QUALIFICATIONS <span class="accent">SUMMARY</span></h2>
  <div class="abs rule" style="top:2704px"></div>
  <p class="abs para light" style="top:2735px;font-size:13.5px">The founders of Velmo Trail OÜ bring forth a wealth of experience and expertise to the table. A former USAF Combat Controller, with nearly a decade of service in Europe; and a highly esteemed former Estonian Special Operator who graduated BUDs and Ranger School, with a proven track record of business success in Estonia. Together, we are steadfast in our dedication to delivering world-class training experiences, deeply rooted in operational excellence and strategic foresight.</p>

  <form>
    <div class="abs field" style="left:180px;top:2879px;width:408px"><svg width="11" height="12" viewBox="0 0 12 13"><circle cx="6" cy="4" r="3" fill="none" stroke="#8a8f98" stroke-width="1.3"/><path d="M1 12c0-3 2.5-4.5 5-4.5s5 1.5 5 4.5z" fill="none" stroke="#8a8f98" stroke-width="1.3"/></svg>First Name</div>
    <div class="abs field" style="left:611px;top:2879px;width:408px"><svg width="11" height="12" viewBox="0 0 12 13"><circle cx="6" cy="4" r="3" fill="none" stroke="#8a8f98" stroke-width="1.3"/><path d="M1 12c0-3 2.5-4.5 5-4.5s5 1.5 5 4.5z" fill="none" stroke="#8a8f98" stroke-width="1.3"/></svg>Last Name</div>
    <div class="abs field" style="left:180px;top:2949px;width:408px"><svg width="13" height="11" viewBox="0 0 14 11"><rect x="0" y="0" width="14" height="11" rx="1" fill="#8a8f98"/><path d="M1 1l6 5 6-5" fill="none" stroke="#fff" stroke-width="1.2"/></svg>Email Address</div>
    <div class="abs field" style="left:611px;top:2949px;width:408px"><svg width="11" height="11" viewBox="0 0 24 24"><path fill="#8a8f98" d="M6.6 10.8a15.1 15.1 0 0 0 6.6 6.6l2.2-2.2a1 1 0 0 1 1-.25 11.4 11.4 0 0 0 3.6.57 1 1 0 0 1 1 1V20a1 1 0 0 1-1 1A17 17 0 0 1 3 4a1 1 0 0 1 1-1h3.5a1 1 0 0 1 1 1c0 1.25.2 2.45.57 3.57a1 1 0 0 1-.25 1z"/></svg>Phone number</div>
    <div class="abs field" style="left:180px;top:3019px;width:839px;height:104px"><svg width="13" height="11" viewBox="0 0 14 12"><ellipse cx="7" cy="5" rx="7" ry="5" fill="#8a8f98"/><path d="M2 8l-1 4 4-2z" fill="#8a8f98"/></svg>Message</div>
    <div class="abs button">SUBMIT NOW <svg width="14" height="14" viewBox="0 0 14 14"><circle cx="7" cy="7" r="7" fill="#fff"/><path d="M5.5 4l3 3-3 3" fill="none" stroke="#4a7aab" stroke-width="1.8"/></svg></div>
  </form>
</section>

<section>
  <h2 class="abs heading" style="top:3308px"><span class="accent">OUR</span> GALLERY</h2>
  <div class="abs rule" style="top:3360px;left:540px;width:120px"></div>
  <div class="abs tile" style="left:143px;top:3412px;width:216px;height:276px;background:linear-gradient(180deg,#c7d0d9 0%,#aab6c2 70%,#8d8067 100%)" role="img" aria-label="Photo of a helicopter with paratroopers descending over a field"></div>
  <div class="abs tile" style="left:375px;top:3412px;width:216px;height:276px;background:linear-gradient(180deg,#4d5a3a,#6c7c4a 60%,#4a5536)" role="img" aria-label="Photo of two operators reviewing a map on a tablet in grass"></div>
  <div class="abs tile" style="left:607px;top:3412px;width:447px;height:276px;background:linear-gradient(180deg,#c9a15c 0%,#8d6a3f 40%,#3b3530 75%,#25272b 100%)" role="img" aria-label="Photo of troops boarding tiltrotor aircraft on a flight deck at sunset"></div>
  <div class="abs tile" style="left:143px;top:3717px;width:446px;height:276px;background:linear-gradient(180deg,#6e8a58 0%,#8aa26c 50%,#55693f 100%)" role="img" aria-label="Photo of a helicopter landing on a green field with soldier in foreground"></div>
  <div class="abs tile" style="left:607px;top:3717px;width:216px;height:276px;background:linear-gradient(180deg,#8fb2d3 0%,#aac4dc 50%,#7b93a8 100%)" role="img" aria-label="Photo of a skydiver in free fall above clouds"></div>
  <div class="abs tile" style="left:840px;top:3717px;width:215px;height:276px;background:linear-gradient(180deg,#6f8153 0%,#5c5a48 55%,#6b3a32 100%)" role="img" aria-label="Photo of soldiers on a training mat outdoors"></div>
  <div class="abs dots"><span></span><span class="on"></span><span></span></div>
</section>

<footer class="abs footer">
  <p class="abs copy">Copyright© 2024 Velmotrail | All Rights Reserved</p>
  <span class="abs code">C70</span>
</footer>

</body>
</html>
```